Copper Lantern

Need a business card for our restaurant. Restaurant and Bar in the mountains of North Idaho. Rustic looking card

rustic design, wood and metal looking, primarily neutral colors

• Name, address, phone number, website, email address

```html
<!DOCTYPE html>
<html lang="en">
<head>
<meta charset="utf-8">
<title>Copper Lantern – Business Card</title>
<link href="https://fonts.googleapis.com/css2?family=Montserrat:wght@400;500;700&display=swap" rel="stylesheet">
<style>
  :root {
    --backdrop: #2a2a2b;
    --card-light: #1e1d1c;
    --card-dark: #111111;
    --card-edge: #262422;
    --gloss: #4a4744;
    --metal: #8a847d;
    --ink: #f2f2f2;
    --ink-soft: #cfcfcf;
    --deco-top: #3d3b38;
    --deco-bottom: #0e0d0c;
  }
  * { box-sizing: border-box; margin: 0; padding: 0; }
  html, body { width: 1200px; height: 875px; overflow: hidden; }
  body {
    background: var(--backdrop);
    font-family: "Montserrat", sans-serif;
    color: var(--ink);
    position: relative;
  }
  .card {
    position: absolute;
    top: 282px;
    width: 540px;
    height: 310px;
    background: linear-gradient(135deg, var(--card-light) 0%, var(--card-dark) 55%, var(--card-light) 100%);
    border: 1px solid var(--card-edge);
    border-radius: 18px;
    overflow: hidden;
    box-shadow: 0 14px 30px rgba(0,0,0,.45);
  }
  .card--front { left: 30px; }
  .card--back { left: 630px; }

  /* Front */
  .front-gloss {
    position: absolute;
    left: 0; top: 0; bottom: 0;
    width: 110px;
    background: linear-gradient(90deg, rgba(255,255,255,.07), rgba(255,255,255,0));
  }
  .front-seal {
    position: absolute;
    left: 50%; top: 50%;
    width: 190px; height: 190px;
    transform: translate(-50%, -50%);
    border: 5px solid var(--gloss);
    border-radius: 50%;
    display: flex; align-items: center; justify-content: center;
  }
  .front-seal__name {
    font-weight: 500;
    font-size: 19px;
    letter-spacing: 2px;
    text-transform: uppercase;
    text-align: center;
    line-height: 1.3;
    color: var(--metal);
  }

  /* Back */
  .back-seal {
    position: absolute;
    left: 46px; top: 62px;
    width: 104px; height: 104px;
    border: 3px solid var(--ink);
    border-radius: 50%;
    display: flex; align-items: center; justify-content: center;
  }
  .back-seal__name {
    font-weight: 500;
    font-size: 11.5px;
    letter-spacing: 1.5px;
    text-transform: uppercase;
    text-align: center;
    line-height: 1.3;
    color: var(--ink);
  }
  .person {
    position: absolute;
    right: 160px; top: 30px;
  }
  .person__name { font-weight: 700; font-size: 21px; }
  .person__role { font-weight: 500; font-size: 12px; color: var(--ink-soft); margin-top: 1px; padding-left: 20px; }
  .mascot-area {
    position: absolute;
    right: 30px; top: 92px;
    width: 170px; height: 190px;
    border-radius: 12px;
    background: linear-gradient(160deg, var(--deco-top), var(--deco-bottom));
    opacity: .85;
  }
  .contact {
    position: absolute;
    left: 46px; bottom: 24px;
    font-size: 12.5px;
    line-height: 1.45;
    color: var(--ink);
  }
  .contact__address { margin-bottom: 8px; }
  .contact__row { display: flex; align-items: center; gap: 8px; margin-left: 30px; }
  .contact__icon { width: 12px; height: 12px; fill: var(--ink); flex: none; }
</style>
</head>
<body>
  <section class="card card--front" aria-label="Card front">
    <div class="front-gloss"></div>
    <div class="front-seal">
      <span class="front-seal__name">Copper<br>Lantern</span>
    </div>
  </section>

  <section class="card card--back" aria-label="Card back">
    <div class="person">
      <p class="person__name">Evan Marsh</p>
      <p class="person__role">Managing Director</p>
    </div>

    <div class="mascot-area" role="img" aria-label="Large dark glossy mascot silhouette decoration"></div>

    <div class="back-seal">
      <span class="back-seal__name">Copper<br>Lantern</span>
    </div>

    <div class="contact">
      <p class="contact__address">48 Timber Road,<br>Pinecrest, USA</p>
      <p class="contact__row">
        <svg class="contact__icon" viewBox="0 0 24 24" aria-hidden="true"><path d="M6.6 10.8a15.2 15.2 0 0 0 6.6 6.6l2.2-2.2a1 1 0 0 1 1-.25 11.4 11.4 0 0 0 3.6.57 1 1 0 0 1 1 1V20a1 1 0 0 1-1 1A17 17 0 0 1 3 4a1 1 0 0 1 1-1h3.5a1 1 0 0 1 1 1c0 1.25.2 2.45.57 3.57a1 1 0 0 1-.25 1z"/></svg>
        (08) 5550 1472
      </p>
      <p class="contact__row">
        <svg class="contact__icon" viewBox="0 0 24 24" aria-hidden="true"><path d="M2 5h20v14H2z M3 6l9 7 9-7" fill="none" stroke="#f2f2f2" stroke-width="2"/></svg>
        info@copperlanternbar.com
      </p>
      <p class="contact__row">
        <svg class="contact__icon" viewBox="0 0 24 24" aria-hidden="true"><circle cx="12" cy="12" r="10"/></svg>
        www.copperlanternbar.com
      </p>
    </div>
  </section>
</body>
</html>
```